Specialised investor in e-mobility and energy wants business card design

We need a business card design that fits our existing corporate design. <The look and feel must be 'sharp'/'clean', dynamic, communicate momentum, professionalism etc (as one would imagine from a firm in the financial sector). We like the idea of a reverse-side of the card that includes the logo, and the name and contact details on the other. We expect the deliverable to be whatever format might be required to be able to get cards printed directly by a service such as kelmo press. Our website is www.zub.capital

```html
<!DOCTYPE html>
<html lang="en">
<head>
<meta charset="utf-8">
<title>Zub Capital — Business Card</title>
<link rel="stylesheet" href="https://fonts.googleapis.com/css2?family=Arimo:wght@400;700&display=swap">
<style>
  :root {
    --backdrop: #262626;
    --card-white: #ffffff;
    --green-dark: #344f24;
    --green-light: #7bb143;
    --text-grey: #333333;
    --on-dark: #ffffff;
  }
  * { margin: 0; padding: 0; box-sizing: border-box; }
  html, body {
    width: 1200px;
    height: 1059px;
    overflow: hidden;
    background: var(--backdrop);
    font-family: "Arimo", Arial, sans-serif;
  }
  .canvas { position: relative; width: 1200px; height: 1059px; }

  .card {
    position: absolute;
    width: 690px;
    height: 392px;
    border-radius: 18px;
    overflow: hidden;
  }
  .card--front { left: 256px; top: 89px; background: var(--card-white); }
  .card--back  { left: 254px; top: 547px; background: var(--green-dark); }

  /* Front */
  .brand {
    position: absolute;
    display: flex;
    align-items: center;
    gap: 12px;
    left: 48px;
    top: 170px;
    width: 270px;
    color: var(--green-dark);
    font-size: 40px;
    font-weight: 400;
    white-space: nowrap;
  }
  .brand__mark {
    width: 16px; height: 16px;
    background: var(--green-light);
    flex: none;
  }
  .divider {
    position: absolute;
    left: 344px; top: 111px;
    width: 1px; height: 169px;
    background: var(--green-dark);
  }
  .details {
    position: absolute;
    left: 375px; top: 105px;
    color: var(--text-grey);
    font-size: 16px;
    line-height: 20px;
  }
  .details__name {
    font-size: 28px;
    line-height: 30px;
    font-weight: 700;
    letter-spacing: 0.3px;
    color: var(--green-dark);
  }
  .details__name span { color: var(--green-light); }
  .details__role { margin-bottom: 12px; }
  .details__address { margin-bottom: 15px; }
  .contact { list-style: none; }
  .contact li {
    display: flex;
    align-items: center;
    gap: 7px;
    height: 23px;
  }
  .contact svg { width: 12px; height: 12px; flex: none; }

  /* Back */
  .brand.brand--large {
    left: 0;
    top: 148px;
    width: 100%;
    justify-content: center;
    gap: 20px;
    color: var(--on-dark);
    font-size: 84px;
    line-height: 97px;
  }
  .brand--large .brand__mark { width: 30px; height: 30px; }
</style>
</head>
<body>
<main class="canvas">

  <section class="card card--front" aria-label="Card front">
    <div class="brand">
      <span class="brand__mark"></span>
      <span class="brand__name">Zub Capital</span>
    </div>

    <div class="divider"></div>

    <div class="details">
      <p class="details__name">MARTEN <span>OSKAR</span></p>
      <p class="details__role">Director/Founder</p>
      <p class="details__address">1234 Street Name<br>Country Name AB 5748</p>
      <ul class="contact">
        <li>
          <svg viewBox="0 0 12 12" aria-hidden="true"><path fill="#7bb143" d="M2.5 1 L4.5 1 L5.2 3.5 L4 4.5 C4.6 6 6 7.4 7.5 8 L8.5 6.8 L11 7.5 L11 9.5 C11 10.3 10.3 11 9.5 11 C5 11 1 7 1 2.5 C1 1.7 1.7 1 2.5 1 Z"/></svg>
          123-480-2291
        </li>
        <li>
          <svg viewBox="0 0 12 12" aria-hidden="true"><rect x="0.5" y="2" width="11" height="8" fill="#7bb143"/><path d="M0.5 2.5 L6 6.5 L11.5 2.5" fill="none" stroke="#ffffff" stroke-width="1"/></svg>
          info@zub.capital
        </li>
        <li>
          <svg viewBox="0 0 12 12" aria-hidden="true"><circle cx="6" cy="6" r="5.5" fill="#7bb143"/><path d="M3 3.5 C4.5 4 4 6 5.5 6.5 C6 8 5 9 5.5 10.5 M8 2 C7.5 3.5 9 4 10 4.5" fill="none" stroke="#ffffff" stroke-width="1"/></svg>
          www.zub.capital
        </li>
      </ul>
    </div>
  </section>

  <section class="card card--back" aria-label="Card back">
    <div class="brand brand--large">
      <span class="brand__mark"></span>
      <span class="brand__name">Zub Capital</span>
    </div>
  </section>

</main>
</body>
</html>
```